Maris Dovey Studio Business Cards

Hi - using the information and logo provided I require a two sided business card designed with the following information. The business card is a 'mini card' 3.5" x 1.25".

Front of card should be the logo attached but inverted (so the background is the peach colour and the logo white).

Back should have these details. If we can't fit the Pictogrum and Friendwall part can we just put the little logos.

Tessa Varnold

Art and Design Consultant
Dealer - Curator - Events - Styling - Creative Sourcing

P: 0438 217 604
E: tessa@marisdoveystudio.example
W: www.marisdoveystudio.example
I (pictogram image please): marisdoveystudio F (Friendwall image please): MarisDoveyAdviser

Target Market(s)

Galleries, artists, art buyers, interior design clients, event managers, creative types

Industry/Entity Type

Business

```html
<!DOCTYPE html>
<html lang="en">
<head>
<meta charset="utf-8">
<title>Maris Dovey Studio – Mini Business Cards</title>
<link rel="stylesheet" href="https://fonts.googleapis.com/css2?family=Tinos&family=Marcellus&family=Arimo&display=swap">
<style>
  :root {
    --stage: #8e8e8e;
    --peach: #f4b99c;
    --paper: #ffffff;
    --ink-grey: #6b6b6b;
    --ink-dark: #3a3a3a;
    --rule: #dcdcdc;
  }
  html, body {
    margin: 0;
    padding: 0;
    width: 1200px;
    height: 1200px;
    overflow: hidden;
    background: var(--stage);
  }
  .canvas {
    position: relative;
    width: 1200px;
    height: 1200px;
  }
  .card {
    position: absolute;
    top: 108px;
    width: 353px;
    height: 984px;
    text-align: center;
  }
  .card--front { left: 186px; background: var(--peach); color: var(--paper); }
  .card--back  { left: 659px; background: var(--paper); }

  .brand-mark {
    position: absolute;
    left: 0;
    right: 0;
  }
  .brand-mark svg { display: block; margin: 0 auto; }
  .brand-name {
    margin: 0;
    font-family: "Tinos", serif;
    text-transform: uppercase;
    line-height: 1.35;
  }
  .card--front .brand-mark { top: 90px; }
  .card--front .brand-name {
    margin-top: 30px;
    font-size: 27px;
    letter-spacing: 5px;
    color: var(--paper);
  }
  .card--back .brand-mark { top: 96px; }
  .card--back .brand-name {
    margin-top: 14px;
    font-size: 15px;
    letter-spacing: 4px;
    color: var(--peach);
  }

  .services {
    position: absolute;
    top: 478px;
    left: 0;
    right: 0;
    margin: 0;
    padding: 0;
    list-style: none;
    font-family: "Tinos", serif;
    font-size: 29px;
    text-transform: uppercase;
    color: var(--paper);
  }
  .services li { height: 62.6px; line-height: 62.6px; }

  .person {
    position: absolute;
    top: 232px;
    left: 0;
    right: 0;
  }
  .person__name {
    margin: 0;
    font-family: "Marcellus", serif;
    font-weight: 400;
    font-size: 38px;
    color: var(--peach);
  }
  .person__role {
    margin: 6px 0 0;
    font-family: "Arimo", sans-serif;
    font-size: 23px;
    color: var(--ink-grey);
  }
  .divider {
    position: absolute;
    top: 374px;
    left: 27px;
    right: 27px;
    border: 0;
    border-top: 2px solid var(--rule);
    margin: 0;
  }
  .contact {
    position: absolute;
    top: 592px;
    left: 0;
    right: 0;
    margin: 0;
    font-family: "Arimo", sans-serif;
    font-size: 20px;
    color: var(--ink-dark);
    font-style: normal;
  }
  .contact p { margin: 0; height: 43.5px; line-height: 43.5px; }

  .social {
    position: absolute;
    top: 876px;
    left: 43px;
    margin: 0;
    padding: 0;
    list-style: none;
    font-family: "Arimo", sans-serif;
    font-size: 20px;
    color: var(--ink-dark);
    text-align: left;
  }
  .social li {
    display: flex;
    align-items: center;
    height: 45px;
  }
  .social__badge {
    width: 28px;
    height: 28px;
    background: var(--peach);
    margin-right: 16px;
    flex: none;
  }
</style>
</head>
<body>
<main class="canvas">

  <section class="card card--front" aria-label="Card front">
    <div class="brand-mark">
      <svg width="92" height="92" viewBox="0 0 92 92" aria-hidden="true">
        <circle cx="46" cy="46" r="43" fill="none" stroke="var(--paper)" stroke-width="4"/>
      </svg>
      <p class="brand-name">Maris Dovey<br>Studio</p>
    </div>
    <ul class="services">
      <li>Dealer</li>
      <li>Curator</li>
      <li>Events</li>
      <li>Styling</li>
      <li>Creative</li>
      <li>Sourcing</li>
    </ul>
  </section>

  <section class="card card--back" aria-label="Card back">
    <div class="brand-mark">
      <svg width="64" height="64" viewBox="0 0 64 64" aria-hidden="true">
        <circle cx="32" cy="32" r="32" fill="var(--peach)"/>
      </svg>
      <p class="brand-name">Maris Dovey Studio</p>
    </div>
    <div class="person">
      <h1 class="person__name">Tessa Varnold</h1>
      <p class="person__role">Art and Design Consultant</p>
    </div>
    <hr class="divider">
    <address class="contact">
      <p>0438 217 604</p>
      <p>tessa@marisdoveystudio.example</p>
      <p>www.marisdoveystudio.example</p>
    </address>
    <ul class="social">
      <li><span class="social__badge" aria-hidden="true"></span>marisdoveystudio</li>
      <li><span class="social__badge" aria-hidden="true"></span>MarisDoveyAdviser</li>
    </ul>
  </section>

</main>
</body>
</html>
```